Animal Horse & Bedding Company Needs a Website Coded & Designed

We need a website for a new animal bedding and feed company that is visually grabbing and vibrant. We would like to see a website that displays trust, quality and confidence. Needs to be responsive and mobile friendly for all browsers and coded for both Android & IOS. SEO is also important.

Joomla or Wordpress – must be both desktop and mobile friendly with fast page load speed. Need the ability to edit ourselves in Wordpress or Joomla.

Full details attached below with some layout and content ideas.

Coding

Coded - Design and coding required

Number of Pages Required

5+ page

Font styles to use
Sans Serif

Requirements
Must have
• Needs to be responsive and mobile friendly for all browsers and coded for both Android & IOS. SEO is also important.

Wordpress – must be both desktop and mobile friendly with fast page load speed. Need the ability to edit ourselves in Wordpress.

Logo Colours:
Dark Brown
CMYK: 50 / 70 / 80 / 70
Pantone: 4625C

Orange
CMYK: 0 / 50 / 100 / 0
Pantone: 144C
Nice to have
• Use picture of building attached and super impose logo on building.

```html
<!DOCTYPE html>
<html lang="en">
<head>
<meta charset="utf-8">
<title>Golden Bale – Bedding &amp; Feed</title>
<link href="https://fonts.googleapis.com/css2?family=Bebas+Neue&family=Poppins:wght@400;500;600&display=swap" rel="stylesheet">
<style>
:root{
  --brown:#3a2415;
  --brown-deep:#2b1a0f;
  --orange:#f7941d;
  --white:#ffffff;
  --cream:#f3e9dc;
  --ink:#2a2a2a;
  --stage:#f2efea;
}
*{margin:0;padding:0;box-sizing:border-box}
html,body{width:1200px;height:3158px;overflow:hidden}
body{background:var(--stage);font-family:"Poppins",sans-serif;color:var(--ink);position:relative}
.page{position:absolute;left:0;top:335px;width:1200px;height:2487px;background:var(--white);overflow:hidden}
.abs{position:absolute}
.display{font-family:"Bebas Neue",sans-serif;font-weight:400;letter-spacing:1px}

/* header */
.site-header{left:0;top:0;width:1200px;height:100px;background:linear-gradient(90deg,#3b2516,#4a2f1c 50%,#3b2516)}
.contact-line{left:84px;font-size:11px;color:var(--white);display:flex;align-items:center;gap:14px}
.brand{left:0;top:0;width:1200px;height:100px;display:flex;align-items:center;justify-content:center;gap:10px}
.brand-mark{width:14px;height:14px;background:var(--orange)}
.brand-name{font-family:"Bebas Neue",sans-serif;font-size:34px;color:var(--white);letter-spacing:2px}
.search{left:865px;top:37px;width:267px;height:29px;background:var(--white);border-radius:3px;font-size:10px;color:#aaa;padding:8px 16px}
.search svg{position:absolute;right:14px;top:9px}
.main-nav{left:0;top:100px;width:1200px;height:36px;background:var(--orange)}
.main-nav a{position:absolute;top:9px;transform:translateX(-50%);font-size:14px;color:var(--white);text-decoration:none}

/* hero */
.hero{left:0;top:136px;width:1200px;height:587px;background:linear-gradient(180deg,#c9b27a 0%,#e7b65a 35%,#c9a84a 55%,#8fae45 78%,#b9c83a 100%)}
.hero-welcome{left:95px;top:264px;font-size:40px;color:var(--white)}
.hero-title{left:93px;top:330px;font-size:108px;line-height:1;color:var(--white)}
.hero-sub{left:95px;top:432px;font-size:56px;color:var(--white);letter-spacing:3px}
.btn{display:flex;align-items:center;justify-content:center;background:var(--orange);color:var(--white);font-family:"Bebas Neue",sans-serif;font-size:17px;letter-spacing:2px;border-radius:2px;box-shadow:0 3px 4px rgba(0,0,0,.2)}

/* about */
.about-art{left:154px;top:796px;width:254px;height:348px;border-radius:50% 50% 46% 46%;background:radial-gradient(circle at 50% 60%,#d6c3a2,#7a5230 70%,#4a2f1c)}
.about-title{left:581px;top:818px;font-size:50px;color:var(--brown)}
.about-rule{left:581px;top:882px;width:78px;height:4px;background:var(--brown)}
.about-text{left:581px;top:910px;width:470px;font-size:12.5px;line-height:21px;color:var(--ink)}

/* benefits */
.band{left:0;width:1200px}
.bedding-band{top:1232px;height:388px;background:linear-gradient(180deg,#5d6a63 0%,#6e7f5a 45%,#5f9a36 75%,#4f8a2a 100%)}
.feed-band{top:1620px;height:388px;background:linear-gradient(180deg,#2f5a2a 0%,#4f8a33 35%,#6ca53c 70%,#5a9530 100%)}
.benefit-box{border:1.5px solid var(--orange);background:rgba(28,32,30,.72)}
.benefit-title{font-size:52px;color:var(--white);letter-spacing:2px}
.benefit-list{font-size:10.5px;line-height:15px;color:var(--white);list-style:none;letter-spacing:.4px}
.benefit-list li{padding-left:8px;text-indent:-8px}
.benefit-list li::before{content:"• "}

/* newsletter */
.footer{left:0;top:2038px;width:1200px;height:449px;background:var(--brown)}
.subscribe{left:137px;top:2076px;width:925px;height:89px;background:var(--orange)}
.subscribe-label{left:172px;top:2106px;font-size:25px;color:var(--brown)}
.subscribe-input{left:454px;top:2103px;width:408px;height:36px;background:var(--white);font-size:12px;color:#999;padding:10px 16px}
.subscribe-btn{left:878px;top:2103px;width:162px;height:36px;background:var(--brown-deep);color:var(--white);font-size:19px;display:flex;align-items:center;justify-content:center}

/* footer */
.foot-brand{left:162px;top:2252px;width:200px;text-align:center;display:flex;align-items:center;justify-content:center;gap:8px}
.foot-brand .brand-name{font-size:30px}
.foot-about{left:162px;top:2318px;width:220px;font-size:12px;line-height:18px;color:var(--cream);letter-spacing:.6px}
.foot-head{font-size:18px;font-weight:500;color:var(--white);letter-spacing:.5px}
.foot-small{font-size:11px;color:var(--white);letter-spacing:.5px}
.foot-links{left:674px;top:2280px;list-style:none;font-size:11.5px;line-height:21px;color:var(--white);font-weight:500}
.social{display:flex;align-items:center;gap:18px;font-size:11px;color:var(--white)}
.social i{width:14px;height:14px;background:var(--white);border-radius:50%;display:block}
.foot-rule{left:137px;top:2452px;width:925px;height:1px;background:#8a7462}
.copyright{left:0;top:2464px;width:1200px;text-align:center;font-size:11px;color:var(--white)}
</style>
</head>
<body>
<main class="page">

  <header class="abs site-header">
    <div class="abs contact-line" style="top:32px">
      <svg width="12" height="12" viewBox="0 0 24 24"><path fill="#f7941d" d="M6.6 10.8a15 15 0 0 0 6.6 6.6l2.2-2.2c.3-.3.7-.4 1-.2 1.1.4 2.3.6 3.6.6.6 0 1 .4 1 1V20c0 .6-.4 1-1 1A17 17 0 0 1 3 4c0-.6.4-1 1-1h3.5c.6 0 1 .4 1 1 0 1.3.2 2.5.6 3.6.1.3 0 .7-.2 1z"/></svg>
      <span>0800-555-0142</span>
    </div>
    <div class="abs contact-line" style="top:56px">
      <svg width="12" height="10" viewBox="0 0 24 18"><rect width="24" height="18" rx="2" fill="#f7941d"/><path d="M1 2l11 8 11-8" stroke="#3a2415" stroke-width="2" fill="none"/></svg>
      <span>hello@goldenbale.example</span>
    </div>
    <div class="abs brand"><span class="brand-mark"></span><span class="brand-name">Golden Bale</span></div>
    <div class="abs search">Search
      <svg width="10" height="10" viewBox="0 0 24 24"><circle cx="10" cy="10" r="7" stroke="#f7941d" stroke-width="3" fill="none"/><path d="M15 15l7 7" stroke="#f7941d" stroke-width="3"/></svg>
    </div>
  </header>

  <nav class="abs main-nav">
    <a href="#" style="left:288px">Home</a>
    <a href="#" style="left:390px">About</a>
    <a href="#" style="left:487px">Feed</a>
    <a href="#" style="left:594px">Bedding</a>
    <a href="#" style="left:723px">Contact Us</a>
    <a href="#" style="left:876px">Requets Quote</a>
  </nav>

  <section class="abs hero" role="img" aria-label="Chestnut horse standing in a sunlit meadow with wildflowers"></section>
  <div class="abs display hero-welcome">Wellcome</div>
  <h1 class="abs display hero-title">Golden Bale</h1>
  <div class="abs display hero-sub">Bedding &amp; Feed</div>
  <a class="abs btn" style="left:94px;top:506px;width:136px;height:32px">Shop Now</a>

  <section>
    <div class="abs about-art" role="img" aria-label="Illustration of a horseshoe with a wheat stalk growing through it"></div>
    <h2 class="abs display about-title">About Us</h2>
    <div class="abs about-rule"></div>
    <p class="abs about-text">Looking for the best bedding and feed for your horse, livestock or household pet look no further.&nbsp; We use premium locally sourced straw and hay in all of our products and are committed in providing quality products and service.<br>Your animal deserves the very best in health and comfort to keep them healthy, strong and happy.&nbsp; Our products are designed for horses, livestock (goats, cattle and sheep), small caged animals (rabbits, guinea pigs and more).</p>
    <a class="abs btn" style="left:581px;top:1106px;width:132px;height:32px">Learn More</a>
  </section>

  <section class="abs band bedding-band" role="img" aria-label="Young horse in a halter holding a feed bucket on green pasture"></section>
  <div class="abs benefit-box" style="left:53px;top:1282px;width:481px;height:286px"></div>
  <h2 class="abs display benefit-title" style="left:102px;top:1310px">Bedding Benefit</h2>
  <ul class="abs benefit-list" style="left:102px;top:1378px;width:165px">
    <li>100% Natural Chopped Straw</li><li>Low Dust</li><li>Chemical &amp; Additive Free</li><li>Clean &amp; Highly Absorbent</li><li>Cheaper than Wood Shavings</li>
  </ul>
  <ul class="abs benefit-list" style="left:277px;top:1378px;width:240px">
    <li>Economic – less used and less wasted</li><li>Environmentally Friendly – Recyclable &amp; Compostable</li>
  </ul>
  <a class="abs btn" style="left:102px;top:1505px;width:133px;height:32px">Shop Now</a>

  <section class="abs band feed-band" role="img" aria-label="Palomino horse grazing in a fenced paddock"></section>
  <div class="abs benefit-box" style="left:665px;top:1685px;width:480px;height:286px"></div>
  <h2 class="abs display benefit-title" style="left:713px;top:1704px">Feed Benefit</h2>
  <ul class="abs benefit-list" style="left:713px;top:1770px;width:200px">
    <li>100% Natural</li><li>Chemical &amp; Additive Free</li><li>Available in Pellets or Cubes</li><li>High Protein Content</li><li>Eliminate Waste in Feeding</li><li>Clean – Eliminates Dust From Feeding Baled Hay</li>
  </ul>
  <ul class="abs benefit-list" style="left:918px;top:1770px;width:180px">
    <li>Cost Effective</li><li>Convenient</li><li>Less wasted feed</li>
  </ul>
  <a class="abs btn" style="left:713px;top:1908px;width:133px;height:32px">Shop Now</a>

  <footer>
    <div class="abs footer"></div>
    <div class="abs subscribe"></div>
    <div class="abs display subscribe-label">Subscribe for Newsletter</div>
    <div class="abs subscribe-input">Your Email Address</div>
    <div class="abs display subscribe-btn">Subscribe</div>

    <div class="abs foot-brand"><span class="brand-mark"></span><span class="brand-name">Golden Bale</span></div>
    <p class="abs foot-about">Golden Bale offers supply and delivery of fresh bedding as well as removal of waste bedding.</p>

    <div class="abs foot-head" style="left:461px;top:2224px">Get in touch</div>
    <div class="abs foot-small" style="left:461px;top:2283px">0811-555-0101</div>
    <div class="abs foot-small" style="left:461px;top:2326px">022-5550-1188</div>
    <div class="abs foot-small" style="left:461px;top:2372px">0811-555-0177</div>

    <div class="abs foot-head" style="left:674px;top:2224px">Useful Links</div>
    <ul class="abs foot-links">
      <li>Home</li><li>About</li><li>Feed</li><li>Bedding</li><li>Contact Us</li><li>Request Quote</li>
    </ul>

    <div class="abs foot-head" style="left:886px;top:2224px">Connect</div>
    <div class="abs" style="left:886px;top:2260px;font-size:7px;color:var(--cream)">Be apart of Meadowvale family</div>
    <div class="abs social" style="left:886px;top:2285px"><i></i>Snapshare</div>
    <div class="abs social" style="left:886px;top:2313px"><i></i>Friendbook</div>
    <div class="abs social" style="left:886px;top:2341px"><i></i>Chirper</div>
    <div class="abs social" style="left:886px;top:2371px"><i></i>Vidstream</div>

    <div class="abs foot-rule"></div>
    <div class="abs copyright">© Copyright 2020 Golden Bale. All Rights Reserved.</div>
  </footer>

</main>
</body>
</html>
```